Business Card Design for Training Business

Clear Path Coaching is a new business that delivers training and other services with a focus on topics related to mental health and wellbeing, for example, Wellmind Response Course, Resilience etc. We have a strong focus on evidence-based psychology and neuroscience. I have a logo which I will upload with the brief, so please consider colours that work well with the logo.
Target Market(s)
Adults, workplaces (particularly government and not-for-profits)
Industry/Entity Type
Business
Contact Information for Business Card
Head Strong TrainingSamantha SellwoodDirector0438 770 850sam@headstrongtraining.com.auwww.headstrongtraining.com.au

```html
<!DOCTYPE html>
<html lang="en">
<head>
<meta charset="utf-8">
<title>Clear Path Coaching – Business Card</title>
<link rel="stylesheet" href="https://fonts.googleapis.com/css2?family=Arimo:wght@400&family=Josefin+Sans:wght@300&display=swap">
<style>
  :root {
    --page-bg: #e9e7e3;
    --card-teal: #3fb3ad;
    --card-paper: #f6f4ef;
    --arc-taupe: #7d7169;
    --logo-grey: #8c8884;
    --ink: #111111;
  }
  * { box-sizing: border-box; margin: 0; padding: 0; }
  html, body {
    width: 1200px;
    height: 857px;
    overflow: hidden;
    background: var(--page-bg);
  }
  .canvas {
    position: relative;
    width: 1200px;
    height: 857px;
  }
  .card {
    position: absolute;
    left: 100px;
    top: 123px;
    width: 1000px;
    height: 611px;
    border-radius: 6px;
    overflow: hidden;
    box-shadow: 0 10px 30px rgba(0,0,0,0.18);
  }
  .card-shapes {
    position: absolute;
    inset: 0;
    width: 100%;
    height: 100%;
  }
  .card-content {
    position: absolute;
    inset: 0;
    text-align: center;
  }
  .brand-mark {
    position: absolute;
    left: 430px;
    top: 48px;
    width: 140px;
    height: 140px;
    border: 3px solid var(--card-teal);
    border-radius: 50%;
  }
  .brand-name {
    position: absolute;
    left: 0;
    right: 0;
    top: 222px;
    font-family: "Josefin Sans", sans-serif;
    font-weight: 300;
    font-size: 44px;
    letter-spacing: 4px;
    text-transform: uppercase;
    color: var(--logo-grey);
  }
  .person-name {
    position: absolute;
    left: 0;
    right: 0;
    top: 318px;
    font-family: "Arimo", sans-serif;
    font-size: 42px;
    color: var(--ink);
  }
  .person-role {
    position: absolute;
    left: 0;
    right: 0;
    top: 370px;
    font-family: "Arimo", sans-serif;
    font-size: 27px;
    color: var(--ink);
  }
  .contact-list {
    position: absolute;
    left: 0;
    right: 0;
    top: 432px;
    list-style: none;
    font-family: "Arimo", sans-serif;
    font-size: 25px;
    line-height: 36px;
    color: var(--ink);
  }
</style>
</head>
<body>
<main class="canvas">
  <section class="card" aria-label="Business card for Clear Path Coaching">
    <svg class="card-shapes" viewBox="0 0 1000 611" preserveAspectRatio="none" aria-hidden="true">
      <rect class="teal-ground" width="1000" height="611" fill="var(--card-teal)"/>
      <path class="paper-arch" fill="var(--card-paper)"
        d="M0,611 L0,470 C30,250 160,70 300,0 L820,0 C900,60 960,150 1000,240 L1000,611 Z"/>
      <path class="arc-left" fill="var(--arc-taupe)"
        d="M275,28 C135,150 62,380 48,611 L112,611 C118,400 170,200 275,28 Z"/>
      <path class="arc-right" fill="var(--arc-taupe)"
        d="M790,20 C885,130 955,300 1000,535 L1000,400 C950,235 880,115 790,20 Z"/>
    </svg>
    <div class="card-content">
      <div class="brand-mark" aria-hidden="true"></div>
      <p class="brand-name">Clear Path Coaching</p>
      <h1 class="person-name">Rebecca Tanfield</h1>
      <p class="person-role">Director</p>
      <ul class="contact-list">
        <li class="contact-phone">0491 362 517</li>
        <li class="contact-email">bec@clearpathcoaching.example.au</li>
        <li class="contact-web">www.clearpathcoaching.example.au</li>
      </ul>
    </div>
  </section>
</main>
</body>
</html>
```